Landscape design build company door flyer

I would like this flyer to convey a high-level of professionalism for a company that is excellent with communication with their clients as well as a company that does incredible installations

Went on vacation/holiday

```html
<!DOCTYPE html>
<html lang="en">
<head>
<meta charset="utf-8">
<title>Cedar Ridge Builders – Outdoor Living Spaces</title>
<link href="https://fonts.googleapis.com/css2?family=Poppins:wght@400;500;600;700;800&display=swap" rel="stylesheet">
<style>
  :root {
    --navy: #0f2b40;
    --orange: #f26b0c;
    --paper: #e6e6e6;
    --stage: #e9e9e9;
    --ink: #1c1c1c;
    --white: #ffffff;
    --siding: #8e9ea6;
    --cedar: #b08466;
    --forest: #3d5e38;
    --lawn: #4f8f3b;
  }
  * { box-sizing: border-box; margin: 0; padding: 0; }
  html, body { width: 1200px; height: 1029px; overflow: hidden; }
  body { background: var(--stage); font-family: "Poppins", sans-serif; color: var(--ink); position: relative; }

  .flyer { position: absolute; left: 265px; top: 83px; width: 670px; height: 862px; background: var(--paper); overflow: hidden;
    box-shadow: 0 14px 30px rgba(0,0,0,.18); }

  .hero { position: absolute; left: 0; top: 0; width: 670px; height: 469px;
    background:
      radial-gradient(ellipse 260px 300px at 100% 30%, rgba(61,94,56,.95) 0%, rgba(61,94,56,.6) 45%, rgba(61,94,56,0) 100%),
      linear-gradient(180deg, rgba(176,132,102,0) 25%, rgba(176,132,102,.35) 45%, rgba(176,132,102,0) 62%),
      linear-gradient(180deg, #8a9ba4 0%, var(--siding) 40%, #8f9c98 62%, #6f9a63 80%, var(--lawn) 100%); }

  .brand-panel { position: absolute; left: 0; top: 0; width: 351px; height: 146px; background: var(--paper);
    clip-path: polygon(0 0, 351px 0, 276px 146px, 0 146px); }
  .brand-mark { position: absolute; left: 129px; top: 22px; width: 38px; height: 38px; border-radius: 50%; background: var(--orange); }
  .brand-name { position: absolute; left: 0; width: 296px; top: 94px; text-align: center;
    font-size: 15px; font-weight: 500; color: var(--orange); letter-spacing: .3px; line-height: 1; }
  .brand-tagline { position: absolute; left: 0; width: 296px; top: 112px; text-align: center;
    font-size: 7.5px; font-weight: 500; color: var(--navy); letter-spacing: .2px; }

  .project { position: absolute; top: 361px; width: 180px; height: 180px; border-radius: 50%; border: 4px solid var(--white); }
  .project-pavilion { left: 38px; background: linear-gradient(180deg, #9fa7ab 0%, #b98a5a 35%, #7a6e60 65%, #5e6166 100%); }
  .project-deck { left: 246px; background: linear-gradient(180deg, #9aa6ab 0%, #b9bcbb 45%, #a3a8ab 100%); }
  .project-steps { left: 452px; background: linear-gradient(180deg, #8f8a82 0%, #a27a55 45%, #bba07e 100%); }

  .section-title { position: absolute; top: 562px; font-size: 22.5px; font-weight: 800; color: var(--navy); letter-spacing: -.3px; line-height: 1; }
  .section-title::after { content: ""; position: absolute; left: 0; top: 28px; width: 60px; height: 2px; border-radius: 2px; background: var(--orange); }
  .about-title { left: 33px; }
  .services-title { left: 395px; }

  .about-text { position: absolute; left: 32px; top: 604px; width: 303px; font-size: 12px; line-height: 13.7px;
    letter-spacing: .15px; text-align: justify; hyphens: auto; -webkit-hyphens: auto; color: var(--ink); }

  .services { position: absolute; left: 394px; top: 604px; list-style: none; }
  .services li { display: flex; align-items: center; height: 19.4px; font-size: 12.7px; font-weight: 600; color: var(--navy); }
  .services svg { width: 12px; height: 12px; margin-right: 14px; flex: none; }

  .contact-bar { position: absolute; left: 0; top: 777px; width: 670px; height: 85px; }
  .contact-bar svg.bands { position: absolute; inset: 0; }
  .phone-icon { position: absolute; left: 32px; top: 22px; width: 44px; height: 44px; background: var(--orange); display: flex; align-items: center; justify-content: center; }
  .phone-number { position: absolute; left: 85px; top: 18px; font-size: 38px; font-weight: 800; color: var(--white); letter-spacing: -.5px; line-height: 1.2; }
  .contact-line { position: absolute; left: 446px; display: flex; align-items: center; font-size: 12.5px; font-weight: 500; color: var(--white); }
  .contact-line svg { width: 14px; height: 14px; margin-right: 12px; }
  .contact-email { top: 17px; }
  .contact-web { top: 39px; }
</style>
</head>
<body>
  <main class="flyer">
    <div class="hero" role="img" aria-label="Photo of a two-level backyard deck with cedar railings and a staircase beside a grey house, tall evergreens and a lawn"></div>

    <div class="brand-panel">
      <span class="brand-mark"></span>
      <div class="brand-name">CEDAR RIDGE BUILDERS</div>
      <div class="brand-tagline">OUTDOOR LIVING SPACES</div>
    </div>

    <div class="project project-pavilion" role="img" aria-label="Photo of a covered timber pavilion over a stone patio"></div>
    <div class="project project-deck" role="img" aria-label="Photo of a grey composite deck with black metal railing"></div>
    <div class="project project-steps" role="img" aria-label="Photo of a brown composite deck with wraparound steps"></div>

    <h2 class="section-title about-title">ABOUT US</h2>
    <p class="about-text">Discover the endless possibilities for your outdoor space with The Cedar Ridge Builders Team. Our team of skilled artisans is dedicated to turning your outdoor space into a breathtaking oasis that you’ll love coming home to. Whether it’s a cozy patio for intimate gatherings, a sprawling deck to host memorable parties, or a custom paver driveway that adds instant curb appeal, our high-quality craftsmanship ensures stunning results that exceed your expectations.</p>

    <h2 class="section-title services-title">OUR SERVICES</h2>
    <ul class="services">
      <li><svg viewBox="0 0 12 12"><circle cx="6" cy="6" r="6" fill="var(--orange)"/><path d="M3.3 6.2l1.8 1.8 3.6-3.8" fill="none" stroke="#fff" stroke-width="1.5"/></svg>Paver Patios</li>
      <li><svg viewBox="0 0 12 12"><circle cx="6" cy="6" r="6" fill="var(--orange)"/><path d="M3.3 6.2l1.8 1.8 3.6-3.8" fill="none" stroke="#fff" stroke-width="1.5"/></svg>Paver Driveways</li>
      <li><svg viewBox="0 0 12 12"><circle cx="6" cy="6" r="6" fill="var(--orange)"/><path d="M3.3 6.2l1.8 1.8 3.6-3.8" fill="none" stroke="#fff" stroke-width="1.5"/></svg>Retaining Walls</li>
      <li><svg viewBox="0 0 12 12"><circle cx="6" cy="6" r="6" fill="var(--orange)"/><path d="M3.3 6.2l1.8 1.8 3.6-3.8" fill="none" stroke="#fff" stroke-width="1.5"/></svg>Decks &amp; Railings</li>
      <li><svg viewBox="0 0 12 12"><circle cx="6" cy="6" r="6" fill="var(--orange)"/><path d="M3.3 6.2l1.8 1.8 3.6-3.8" fill="none" stroke="#fff" stroke-width="1.5"/></svg>Pools</li>
      <li><svg viewBox="0 0 12 12"><circle cx="6" cy="6" r="6" fill="var(--orange)"/><path d="M3.3 6.2l1.8 1.8 3.6-3.8" fill="none" stroke="#fff" stroke-width="1.5"/></svg>Outdoor Lighting</li>
      <li><svg viewBox="0 0 12 12"><circle cx="6" cy="6" r="6" fill="var(--orange)"/><path d="M3.3 6.2l1.8 1.8 3.6-3.8" fill="none" stroke="#fff" stroke-width="1.5"/></svg>Firepits &amp; Fireplaces</li>
    </ul>

    <footer class="contact-bar">
      <svg class="bands" viewBox="0 0 670 85" preserveAspectRatio="none">
        <rect x="0" y="7" width="420" height="78" fill="var(--navy)"/>
        <polygon points="407,0 670,0 670,85 372,85" fill="var(--orange)"/>
      </svg>
      <div class="phone-icon">
        <svg width="24" height="24" viewBox="0 0 24 24"><path d="M6.6 2.5l3 3.2-1.9 2.6c1.2 2.6 3.3 4.8 6 6l2.6-1.9 3.2 3-1.6 3.3C10.4 19 4.9 13.5 3.3 4.1z" fill="#fff"/></svg>
      </div>
      <div class="phone-number">555-014-2283</div>
      <div class="contact-line contact-email">
        <svg viewBox="0 0 14 14"><rect x="0.5" y="2.5" width="13" height="9" rx="1" fill="#fff"/><path d="M1 3.2l6 4.3 6-4.3" fill="none" stroke="var(--orange)" stroke-width="1.2"/></svg>
        info@cedarridgebuilders.com
      </div>
      <div class="contact-line contact-web">
        <svg viewBox="0 0 14 14" fill="none" stroke="#fff" stroke-width="1"><circle cx="7" cy="7" r="6"/><ellipse cx="7" cy="7" rx="2.6" ry="6"/><path d="M1 7h12"/></svg>
        www.cedarridgebuilders.com
      </div>
    </footer>
  </main>
</body>
</html>
```